Design eines Hausetiketts für traditionelles Weingut
Zielgruppe
Wir das Familienweingut Brandauer in Gimbsheim/Rheinhessen sind ein traditionelles Weingut das seine Reben selbst kultiviert und die Weine auch selbst ausbaut. Wir haben jeden Schritt in der Weinherstellung selbst in der Hand und vermarkten den Wein dann an unsere Privatkunden. Unsere Kundenstruktur sieht folgendermaßen aus: Wir haben 100% Privatkunden die unseren Wein konsumieren. Da jetzt die nächste Generation in den Weinbaubetrieb einsteigt und auch Ideen hat möchten wir ein Hausetikett einführen. Im Moment haben wir noch sehr viele unterschiedliche Etiketten und kein Hausetikett. Da die Verlagsetiketten immer seltener zu unseren Vorstellungen passen, möchten wir hier auf diesem Wege ein Hausetikett anfertigen lassen. Generell möchten wir unseren Außenauftritt komplett modernisieren. Sie können sich über die Vielfalt in unserem Betrieb unter www.weingut-brandauer-beispiel.de einen Überblick verschaffen. Langfristig gesehen wollen wir aber unsere Weinkarte verkleinern.
Aufgabenstellung
Wir haben uns vor ca. 1,5 Jahren hier auf dieser Website bereits ein Logo designen lassen. Es wäre schön wenn man das Logo bei den Entwürfen für die Etiketten berücksichtigen würde. Das wäre aber KEIN MUSS. Auch wäre es gut wenn man das ,,Wein' bei unserem Namen weglassen könnte.
Das Etikett sollte aus Vorder-und Rückenetikett bestehen und edel wirken. Vorne sollte die Rebsorte und die Geschmacksangabe stehen. Der Rest sollte auf das Rückenetikett.
Das Vorderetikett sollte ein richtiger Eyecatcher sein und im Supermarkt z.B. aus vielen anderen herausstechen. Das wäre ganz wichtig.
Man kann bei den Farben unterscheiden in 3 Konzepte.
Literwein als einsteiger Wein
Dann die Gutsweine und zum Schluss die Lagenweine. Alles Farblich oder im design etwas abgesetzt.

```html
<!DOCTYPE html>
<html lang="de">
<head>
<meta charset="utf-8">
<title>Quendral Riesling trocken – Hausetikett</title>
<link rel="stylesheet" href="https://fonts.googleapis.com/css2?family=Amatic+SC:wght@700&family=Open+Sans:wght@400;600&display=swap">
<style>
  :root {
    --page: #ffffff;
    --label-ground: #2a2d34;
    --label-edge: #ffffff;
    --label-outline: #d9d9d9;
    --ink: #ffffff;
  }
  * { margin: 0; padding: 0; box-sizing: border-box; }
  html, body {
    width: 953px;
    height: 1200px;
    overflow: hidden;
    background: var(--page);
  }
  .canvas {
    position: relative;
    width: 953px;
    height: 1200px;
    background: var(--page);
  }
  .front-label {
    position: absolute;
    left: 176px;
    top: 100px;
    width: 600px;
    height: 1000px;
    background: var(--label-ground);
    border: 9px solid var(--label-edge);
    outline: 1px solid var(--label-outline);
    overflow: hidden;
  }
  .producer {
    position: absolute;
    top: 95px;
    left: 0;
    width: 100%;
    text-align: center;
    font-family: "Open Sans", sans-serif;
    font-weight: 600;
    font-size: 24px;
    letter-spacing: 4px;
    color: var(--ink);
  }
  .variety {
    position: absolute;
    left: 88px;
    top: 225px;
    width: 440px;
    font-weight: 700;
  }
  .variety__line {
    display: block;
    height: 205px;
    font-family: "Amatic SC", cursive;
    font-size: 170px;
    line-height: 1;
    color: var(--ink);
    text-transform: uppercase;
    letter-spacing: -2px;
    white-space: nowrap;
    transform: scaleY(1.45);
    transform-origin: left top;
  }
  .vintage {
    position: absolute;
    left: 40px;
    top: 390px;
    font-family: "Open Sans", sans-serif;
    font-size: 28px;
    color: var(--ink);
    transform: rotate(-90deg);
    transform-origin: left top;
  }
  .taste {
    position: absolute;
    right: 100px;
    top: 880px;
    font-family: "Open Sans", sans-serif;
    font-size: 44px;
    line-height: 1;
    color: var(--ink);
  }
</style>
</head>
<body>
  <main class="canvas">
    <section class="front-label" aria-label="Vorderetikett Riesling trocken">
      <p class="producer">QUENDRAL</p>
      <span class="vintage">2019</span>
      <h1 class="variety">
        <span class="variety__line">Riesling</span>
        <span class="variety__line">Riesling</span>
        <span class="variety__line">Riesling</span>
      </h1>
      <p class="taste">trocken</p>
    </section>
  </main>
</body>
</html>
```